Annual review for The Harrow Collective

The Harrow Collective is a small public relations agency in London specialising in corporate and public affairs. Most of our work is international and we have a strong connection to South Africa. We would like to prepare a short annual review for 2016. The review will serve as both a review of our activities in 2016, and as a credentials document. Content then will include:
1. An introduction to the business
2. Who we are
3. Projects and clients undertaken in 2016
4. News and views
We imagine it will be used mostly as a pdf but would like it to be suitable for print. We envisage it to be about 8 pages long. The design look and feel should convey a business, while small, of stature. We shall include some of our client logos but we would welcome the use of some photography / imagery to have visual impact (although we don't have very much of our own!). The corporate look and feel is white, grey and black.

Industry/Entity Type

Public Relation

Font styles to use
Sans Serif

Requirements
Must have
• My project must convey a business with flair and gravitas, that punches above its weight.
Nice to have
• Thoughtful use of imagery.

```html
<!DOCTYPE html>
<html lang="en">
<head>
<meta charset="utf-8">
<title>The Harrow Collective – Annual Review 2016</title>
<link href="https://fonts.googleapis.com/css2?family=Open+Sans:wght@300;400;600;700&display=swap" rel="stylesheet">
<style>
:root{
  --ink:#3a3a3a;
  --body:#4a4a4a;
  --muted:#8a8a8a;
  --accent:#1a9cc4;
  --paper:#ffffff;
  --photo-dark:#4d4d4d;
  --photo-light:#e6e6e6;
}
*{box-sizing:border-box;margin:0;padding:0}
html,body{width:1200px;height:849px;overflow:hidden;background:var(--paper)}
body{font-family:"Open Sans",Arial,sans-serif;color:var(--body);position:relative}
.spread{position:relative;width:1200px;height:849px}
.abs{position:absolute}
.brand{left:57px;top:46px;display:flex;align-items:center;gap:8px;font-weight:700;font-size:15.5px;color:#5a5a5a}
.page-title{font-weight:300;color:var(--ink);font-size:37px;letter-spacing:-.3px}
.lead{font-size:12.3px;line-height:17px;color:var(--ink)}
.copy{font-size:8.6px;line-height:11px;color:var(--body)}
.copy p{margin-bottom:11px}
.photo{background:linear-gradient(135deg,#2c2c2c,#6a6a6a 55%,#3a3a3a)}
.wave{left:600px;top:0;width:600px;height:271px;background:linear-gradient(100deg,#3a3a3a 0%,#6f6f6f 35%,#bdbdbd 60%,var(--photo-light) 80%,#f4f4f4 100%)}
.services{display:grid;grid-template-columns:165px 166px 170px;left:657px;top:390px}
.services h3{color:var(--accent);font-weight:600;font-size:12.2px;margin-bottom:15px}
.services ul{list-style:none;font-size:10.2px;line-height:14px;color:var(--body)}
.services li{padding-left:7px;text-indent:-7px}
.services li::before{content:"• "}
.clients-label{left:657px;top:626px;font-weight:300;font-size:19px;color:var(--ink)}
.client{top:600px;height:80px;display:flex;align-items:center;justify-content:center;gap:6px;font-size:10px;font-weight:600;color:#6a6a6a;text-align:center;line-height:12px}
.client .mark{width:12px;height:12px;background:#8a8a8a;flex:none}
.footer{top:804px;font-size:6.6px;letter-spacing:2px;color:var(--muted)}
.footer .num{color:var(--accent)}
</style>
</head>
<body>
<div class="spread">
  <div class="abs brand">
    <svg width="22" height="22" viewBox="0 0 22 22" aria-hidden="true"><circle cx="11" cy="11" r="9.5" fill="none" stroke="#5a5a5a" stroke-width="1.6"/></svg>
    The Harrow Collective
  </div>
  <h1 class="abs page-title" style="left:56px;top:110px">The partners</h1>

  <p class="abs lead" style="left:57px;top:182px;width:420px">Martin Ashcombe is a corporate and public affairs specialist with a career spanning in-house, consultancy and the charitable sector.</p>
  <div class="abs copy" style="left:57px;top:236px;width:480px">
    <p>At natural resources firm Kestrel Resources, Martin had corporate affairs and government relations responsibility for Europe, Middle East and North Africa on issues relating to its oil and gas operations in the region. Martin served on the directorate team of a leading UK charity advising trustees on strategy, organizational change and stakeholder relations.</p>
    <p>In consultancy, Martin spent six years at Hollis &amp; Grove advising companies such as Meridian Payments, Sunvale Beverages Africa and Aldwick Partners. He also served as a consultant to the Global Capital Development Trust.</p>
    <p>He began his career in politics, working first in the House of Commons, the House of Lords and subsequently the European Parliament. He has served on election observer teams in Hong Kong and Taiwan. He studied in the UK, Germany and South Africa.</p>
  </div>

  <div class="abs photo" role="img" aria-label="Black and white photo of a panel of speakers at a conference table with microphones" style="left:0;top:394px;width:290px;height:174px"></div>

  <p class="abs lead" style="left:308px;top:391px;width:240px">Oliver Prentiss is an international policy expert in sustainable development &amp; business practices, with a focus on water.</p>
  <div class="abs copy" style="left:308px;top:460px;width:240px">
    <p>Previously Oliver worked for ClimateWorks Lab, an EU climate focused innovation and entrepreneurship programme based at Thameside College in London. He moved to Thameside from the International Water Forum in France, where he was the lead policy advisor responsible for projects on water &amp; green growth, ecosystem services, the water-food-energy nexus, &amp; water for development in Africa.</p>
    <p>Oliver also worked at the UK’s Sustainable Futures Commission, reporting directly to the Office of the Prime Minister. He has worked as corporate responsibility analyst at Northgate Bank (NGB) and a risk management consultant for Rowan Baines.</p>
    <p>Oliver has also lectured on environmental management and business policy at Calder College, University of Westmoor. He speaks French, Japanese and Korean, and studied in Australia, New Zealand and the UK.</p>
  </div>

  <div class="abs wave" role="img" aria-label="Black and white photo of a large breaking ocean wave"></div>

  <h2 class="abs page-title" style="left:656px;top:320px;font-size:38px">Our services</h2>
  <div class="abs services">
    <div><h3>Reputation</h3><ul><li>Brand development &amp; strategy</li><li>Issues management</li><li>Public affairs</li><li>Stakeholder engagement</li><li>Litigation PR</li></ul></div>
    <div><h3>Government</h3><ul><li>Government relations – UK, EU and international</li><li>Political risk advisory services</li><li>Political monitoring</li></ul></div>
    <div><h3>Sustainable Development</h3><ul><li>Corporate Social Responsibility management</li><li>Water policy analysis / advisory services</li><li>Environmental policy analysis / advisory services</li></ul></div>
  </div>

  <div class="abs clients-label">Clients</div>
  <div class="abs client" style="left:745px;width:90px"><span class="mark"></span>Animal Care Trust</div>
  <div class="abs client" style="left:845px;width:80px">Karoo University</div>
  <div class="abs client" style="left:950px;width:80px">Water Research Assoc.</div>
  <div class="abs client" style="left:1040px;width:100px">Fenwick Institute</div>

  <div class="abs footer" style="left:57px"><span class="num">03</span> &nbsp;| &nbsp;ANNUAL REVIEW 2016</div>
  <div class="abs footer" style="left:422px">www.harrowcollective.com</div>
  <div class="abs footer" style="left:656px"><span class="num">04</span> &nbsp;| &nbsp;ANNUAL REVIEW 2016</div>
  <div class="abs footer" style="left:1022px">www.harrowcollective.com</div>
</div>
</body>
</html>
```